Creation of an elegant and modern turnkey Shopify website

Hello,

We are a new company specializing in the sale of above-ground pools. We want to create a turnkey website, ideally using Shopify. For now, we need a "showcase" site, not an e-commerce platform, with four tabs:

Home Page (an overall presentation of the company)
Our Products (an overview of all the above-ground pools we sell)
Our Projects (a page inspired by Instagram to showcase photos of our future projects)
Contact (a page with all our contact information and a contact form)

We are looking to create a highly visual, elegant, and modern website with vibrant splashes of color. We will provide the text, photos (along with instructions on where to place them on each page), and all other necessary information as attachments.

Thank you in advance for your proposals!

The Brisa Lagoon Team

Target Market(s)

Targeted at Swiss customers (a translator will need to be installed for different languages)

Industry/Entity Type

Sale of customised above-ground pools

Coding

Coded - Design and coding required

Font styles to use
Sans Serif

Colors
0094D4
00A9DD
6FCCEA
C7EBF8
E9F6FB
00AB8E
00BBA5
67D7C9
C6EFE9
E9F9F6

Requirements
Must have
• A stunning, elegant and modern look
Nice to have
• Inspiration from the colors of our logo throughout the site, but in an elegant way
Should not have
• An overly classic look for swimming pool sites

```html
<!DOCTYPE html>
<html lang="en">
<head>
<meta charset="utf-8">
<title>Brisa Lagoon – Above-Ground Pools</title>
<link href="https://fonts.googleapis.com/css2?family=Lato:wght@400;700&display=swap" rel="stylesheet">
<style>
:root{
  --blue:#0094D4;
  --blue-light:#00A9DD;
  --water:#6FCCEA;
  --water-soft:#C7EBF8;
  --mist:#E9F6FB;
  --grey:#777777;
  --grey-band:#808080;
  --text:#666666;
  --white:#ffffff;
}
*{margin:0;padding:0;box-sizing:border-box}
html,body{width:1200px;height:3490px;overflow:hidden}
body{font-family:'Lato',sans-serif;color:var(--text);background:var(--white);position:relative}
.abs{position:absolute}
.accent{color:var(--blue)}
.btn{position:absolute;display:flex;align-items:center;justify-content:center;width:154px;height:43px;background:var(--blue);color:var(--white);font-size:15px;text-decoration:none}
/* top bar */
.topbar{top:0;left:0;width:1200px;height:38px;font-size:15px;color:var(--grey)}
.topbar span{position:absolute;top:11px;display:flex;align-items:center;gap:8px}
/* nav */
.nav{top:38px;left:0;width:1200px;height:97px;background:var(--blue);color:var(--white)}
.brand{position:absolute;left:111px;top:28px;font-size:22px;letter-spacing:1px;line-height:1.1;text-transform:uppercase}
.menu a{position:absolute;top:38px;color:var(--white);text-decoration:none;font-size:15px}
.nav-tools{position:absolute;right:111px;top:36px;display:flex;gap:22px;align-items:center;font-size:15px}
.photo{position:absolute}
h1,h2,h3{font-weight:700;color:var(--grey)}
.lead{font-weight:700;color:var(--grey);font-size:17px;line-height:1.4}
.body-text{font-size:14.5px;line-height:1.5;color:var(--text)}
/* features */
.feature{position:absolute;width:260px}
.feature svg{display:block;height:72px}
.feature h3{font-size:23px;margin:32px 0 14px;font-weight:400;color:var(--grey)}
.feature p{font-size:14.5px;line-height:1.5}
/* satisfaction */
.sat-left{top:2123px;left:0;width:600px;height:515px;background:var(--mist)}
.sat-right{top:2123px;left:600px;width:600px;height:515px;background:var(--blue);color:var(--white)}
/* contact band */
.contact-band{top:2638px;left:0;width:1200px;height:347px;background:var(--grey-band);color:var(--white);text-align:center}
/* footer */
.fcol{position:absolute;top:3176px;font-size:15px}
.fcol h4{font-size:19px;font-weight:400;color:var(--grey);margin-bottom:22px}
.fcol li{list-style:none;margin-bottom:20px;color:var(--grey)}
</style>
</head>
<body>

<div class="abs topbar">
  <span style="left:111px"><svg width="14" height="16" viewBox="0 0 14 16"><path d="M3 1l3 3-2 2c1 2 3 4 5 5l2-2 3 3-2 3C7 15 0 8 1 3z" fill="var(--blue)"/></svg>079 482 17 30</span>
  <span style="left:417px"><svg width="12" height="16" viewBox="0 0 12 16"><path d="M6 0a6 6 0 0 0-6 6c0 4 6 10 6 10s6-6 6-10a6 6 0 0 0-6-6zm0 8.5A2.5 2.5 0 1 1 6 3.5a2.5 2.5 0 0 1 0 5z" fill="var(--blue)"/></svg>Elena Marchetti Rue des Tilleuls 27 1860 Aigle</span>
  <span style="left:1036px">USD <svg width="12" height="8" viewBox="0 0 12 8"><path d="M1 1l5 5 5-5" stroke="var(--grey)" fill="none" stroke-width="1.5"/></svg></span>
</div>

<header class="abs nav">
  <div class="brand">Brisa<br>Lagoon</div>
  <nav class="menu">
    <a style="left:359px">Home</a>
    <a style="left:489px">Products</a>
    <a style="left:640px">Projects</a>
    <a style="left:785px">Contact</a>
  </nav>
  <div class="nav-tools">
    <svg width="18" height="18" viewBox="0 0 18 18"><circle cx="7.5" cy="7.5" r="5.5" stroke="#fff" stroke-width="2.5" fill="none"/><path d="M12 12l5 5" stroke="#fff" stroke-width="2.5"/></svg>
    <span style="display:flex;gap:8px;align-items:center"><svg width="14" height="16" viewBox="0 0 14 16"><circle cx="7" cy="4" r="4" fill="#fff"/><path d="M0 16c0-5 3-7 7-7s7 2 7 7z" fill="#fff"/></svg>Login</span>
  </div>
</header>

<!-- hero -->
<section>
  <h1 class="abs" style="left:111px;top:240px;width:450px;font-size:43px;line-height:1.06">Transform Your Garden with <span class="accent">Our Premium Above-Ground Pools!</span></h1>
  <p class="abs lead" style="left:111px;top:440px;width:420px">Achieve your dreams with our custom, tailor-made above-ground pools.</p>
  <p class="abs body-text" style="left:111px;top:506px;width:435px">Imagine an exceptional relaxation and leisure space right in your own backyard. With our unparalleled expertise and commitment to excellence, we create above-ground pools that exceed all expectations. Our exclusive, custom-designed models are crafted to combine style, durability, and innovation, offering a unique and refined experience.</p>
  <a class="btn" style="left:111px;top:662px">Read More</a>
  <div class="photo" role="img" aria-label="Aerial view of a swimmer on a pink float in clear turquoise pool water" style="left:592px;top:221px;width:496px;height:513px;background:linear-gradient(135deg,#8fd6ea,#6fcfe3 50%,#a9e0ee)"></div>
  <div class="abs" style="left:811px;top:689px;width:22px;height:22px;background:var(--blue);color:#fff;font-size:12px;text-align:center;line-height:22px">‹</div>
  <div class="abs" style="left:845px;top:689px;width:22px;height:22px;background:var(--blue);color:#fff;font-size:12px;text-align:center;line-height:22px">›</div>
</section>

<!-- services -->
<section>
  <div class="photo" role="img" aria-label="Children playing with an inflatable ring in a pool" style="left:111px;top:821px;width:317px;height:188px;background:linear-gradient(135deg,#3b8fcf,#e6b070 60%,#5aa9d8)"></div>
  <div class="photo" role="img" aria-label="Above-ground pool with a beach ball in a leafy garden" style="left:194px;top:971px;width:398px;height:384px;background:linear-gradient(180deg,#cfe4ef 0%,#6e9a5a 35%,#62b9bd 60%,#3e8f98 100%)"></div>
  <h2 class="abs" style="left:677px;top:938px;font-size:43px">Personalized <span class="accent">Services</span></h2>
  <p class="abs lead" style="left:677px;top:1000px;width:420px">We understand that every garden and client is unique.</p>
  <p class="abs body-text" style="left:677px;top:1043px;width:410px">That's why we offer personalized services, from design to installation and after-sales support. Our team of experts is here to answer all your questions and guide you throughout your project.</p>
  <a class="btn" style="left:677px;top:1169px">Read More</a>
</section>

<!-- why choose -->
<section>
  <h2 class="abs" style="left:113px;top:1434px;width:640px;font-size:43px;line-height:1.05">Why Choose Our &nbsp;<span class="accent">Above-Ground Pools?</span></h2>
  <div class="feature" style="left:111px;top:1590px">
    <svg viewBox="0 0 72 72" width="72"><g stroke="var(--blue)" stroke-width="2.5" fill="none"><path d="M36 3l8 6 10-1 3 9 9 5-3 10 3 10-9 5-3 9-10-1-8 6-8-6-10 1-3-9-9-5 3-10-3-10 9-5 3-9 10 1z"/><circle cx="36" cy="36" r="18"/><path d="M26 42l-2-13 7 6 5-9 5 9 7-6-2 13z"/></g></svg>
    <h3>Superior Quality</h3>
    <p>Each pool is constructed with high-quality materials, ensuring exceptional durability and strength.</p>
  </div>
  <div class="feature" style="left:473px;top:1578px">
    <svg viewBox="0 0 76 76" width="76" height="76"><g stroke="var(--blue)" stroke-width="2.5" fill="none"><rect x="2" y="10" width="50" height="60"/><path d="M2 62h72M30 50l36-36 6 6-36 36-9 3zM72 74V50L50 74z"/></g></svg>
    <h3 style="margin-top:20px">Elegant Design</h3>
    <p>Our pools come in a variety of styles and finishes, seamlessly blending into any garden setting.</p>
  </div>
  <div class="feature" style="left:835px;top:1585px">
    <svg viewBox="0 0 76 76" width="76"><g stroke="var(--blue)" stroke-width="2.5" fill="none"><path d="M38 4l7 2 2 7 7 3 6-3 6 6-3 6 3 7 7 2v9l-7 2-3 7 3 6-6 6-6-3-7 3-2 7h-9l-2-7-7-3-6 3-6-6 3-6-3-7-7-2v-9l7-2 3-7-3-6 6-6 6 3 7-3 2-7z"/><circle cx="38" cy="38" r="18"/><path d="M30 48l3-9 18-18 6 6-18 18z"/></g></svg>
    <h3 style="margin-top:25px">Custom and Tailor-Made</h3>
    <p>Create the pool of your dreams with our customization options, tailored to your specific tastes and needs.</p>
  </div>
  <div class="feature" style="left:111px;top:1840px">
    <svg viewBox="0 0 72 72" width="72"><g stroke="var(--blue)" stroke-width="2.5" fill="none"><path d="M36 3l7 2 2 7 7 3 6-3 6 6-3 6 3 7 7 2v8l-7 2-3 7 3 6-6 6-6-3-7 3-2 7h-8l-2-7-7-3-6 3-6-6 3-6-3-7-7-2v-8l7-2 3-7-3-6 6-6 6 3 7-3 2-7z"/><circle cx="36" cy="36" r="16"/><path d="M28 36l6 6 11-12"/></g></svg>
    <h3>Easy Installation</h3>
    <p>4.Enjoy your new oasis quickly with our simple and fast installation process.</p>
  </div>
  <div class="feature" style="left:473px;top:1833px">
    <svg viewBox="0 0 76 80" width="76" height="80"><g stroke="var(--blue)" stroke-width="2.5" fill="none"><path d="M38 2v8M10 14l6 5M66 14l-6 5M2 40h8M66 40h8"/><path d="M24 58c-6-5-10-12-10-19a24 24 0 0 1 48 0c0 7-4 14-10 19v8H24z"/><path d="M28 72h20M32 78h12"/><circle cx="38" cy="38" r="9"/><circle cx="38" cy="38" r="3"/></g></svg>
    <h3 style="margin-top:22px">Constant Innovation</h3>
    <p>We incorporate the latest technologies to provide you with an optimal and safe swimming experience.</p>
  </div>
</section>

<!-- satisfaction -->
<section>
  <div class="abs sat-left"></div>
  <div class="photo" role="img" aria-label="Two people relaxing on colourful floats in turquoise water, seen from above" style="left:43px;top:2166px;width:506px;height:429px;background:linear-gradient(135deg,#7fd8e8,#4cc3dc 50%,#9fe3ee)"></div>
  <div class="abs sat-right">
    <h2 style="position:absolute;left:85px;top:118px;font-size:43px;color:#fff;white-space:nowrap">Guaranteed Satisfaction</h2>
    <p style="position:absolute;left:85px;top:188px;width:405px;font-size:14.5px;line-height:1.5">Your satisfaction is our top priority. We are committed to providing you with exceptional service and the highest quality products. Join our community of satisfied customers who are already enjoying their custom above-ground pools.</p>
    <p style="position:absolute;left:85px;top:291px;font-size:17px;font-weight:700">10-Year Warranty!</p>
    <a class="btn" style="left:85px;top:347px;background:var(--grey-band)">Read More</a>
  </div>
</section>

<!-- contact band -->
<section class="abs contact-band">
  <h2 style="color:#fff;font-size:43px;margin-top:50px">Contact Us Today</h2>
  <p style="width:800px;margin:28px auto 0;font-size:20px;line-height:1.45">Don't wait any longer to transform your garden into a wellness oasis. Contact us today to discover our range of customizable above-ground pools and get a tailored quote. Dive into a world of infinite possibilities with Brisa Lagoon.</p>
  <a class="btn" style="left:523px;top:236px">Contact Us</a>
</section>

<!-- footer -->
<footer>
  <h2 class="abs" style="left:0;top:3063px;width:1200px;text-align:center;font-size:43px">We Bring Your Pool <span class="accent">Dreams to Life!</span></h2>
  <div class="fcol" style="left:111px">
    <h4>Customer Service</h4>
    <p style="color:var(--blue);text-transform:uppercase;margin-bottom:22px">Brisa Lagoon</p>
    <p style="line-height:1.25;color:var(--grey);margin-bottom:20px">Elena Marchetti<br>Rue des Tilleuls<br>271860 Aigle</p>
    <p style="color:var(--grey)">079 482 17 30</p>
  </div>
  <div class="fcol" style="left:358px"><h4>Our Company</h4><ul><li>Home</li><li>Products</li><li>Projects</li><li>Contact</li></ul></div>
  <div class="fcol" style="left:578px"><h4>Other Links</h4><ul><li>Support</li><li>Help</li><li>Sitemap</li><li>Faq</li></ul></div>
  <div class="fcol" style="left:772px;width:316px">
    <h4>Newsletter</h4>
    <p style="color:var(--grey);line-height:1.6">Excepteur sint occaecat cupidatat non proident, sunt in culpa qui officia deserunt mollit anim id est laborum.</p>
    <div style="position:absolute;top:135px;left:0;width:255px;height:41px;background:#e6e6e6;font-size:13px;color:var(--grey);padding:13px 19px">Email addres</div>
    <div style="position:absolute;top:135px;left:264px;width:52px;height:41px;background:var(--blue);color:#fff;text-align:center;line-height:41px">Get</div>
  </div>
  <p class="abs" style="left:113px;top:3453px;font-size:15px;color:var(--grey)">Copyright © 2024 Brisa Lagoon. All rights reserved.</p>
  <div class="abs" style="left:932px;top:3449px;display:flex;gap:16px">
    <span style="width:24px;height:24px;border-radius:50%;background:var(--grey)"></span>
    <span style="width:24px;height:24px;border-radius:50%;background:var(--grey)"></span>
    <span style="width:24px;height:24px;border-radius:50%;background:var(--grey)"></span>
    <span style="width:24px;height:24px;border-radius:50%;background:var(--grey)"></span>
  </div>
</footer>

</body>
</html>
```